New Brand - Website Design (4 Pages)

We are launching a new brand for electronic cigarettes. We already have logo and packaging done and would like a web design to go with it.

We are interested in the following deliverables:

1) Home Page Design
2) Check Out Design
3) How it Works Page
4) Secondary Template Page Design

Looking for a 60s modern look and something that is consistent with our logo and packaging.

Industry/Entity Type

Electronic

Requirements
Must have
• Consistent with logo and packaging (Use Logo Attached)
White background

Example (Functionality & Design): http://www.moltrafen.co.uk/
Example (Design): http://www.brendolark.com/

We want the design more like brendolark but the functionality the same as moltrafen.

Top Bar: Pale Dunes Kits; Cartridge Refills; How it Works; Contact; My Account; Checkout
Should not have
• Stock List or Search Bar or Newsletter Signup

```html
<!DOCTYPE html>
<html lang="en">
<head>
<meta charset="utf-8">
<title>Pale Dunes – Home</title>
<link rel="stylesheet" href="https://fonts.googleapis.com/css2?family=Ubuntu:wght@300;400;500&family=Ubuntu+Condensed&display=swap">
<style>
:root{
  --page:#ececec;
  --panel:#fbfbfc;
  --ink:#444;
  --soft:#777;
  --blue:#1e9bd7;
  --sky:#5cc3ee;
  --nav-top:#3a3a3a;
  --nav-bot:#0c0c0c;
  --gold:#ffb400;
  --gold-dark:#f39a00;
  --rule:#e3e3e3;
  --foot-top:#5a5a5a;
  --foot-bot:#3a3a3a;
}
*{box-sizing:border-box;margin:0;padding:0}
html,body{width:800px;height:1200px;overflow:hidden}
body{background:var(--page);font-family:"Ubuntu",sans-serif;color:var(--ink);position:relative}
.abs{position:absolute}
a{color:inherit;text-decoration:none}

.brand{left:88px;top:20px;display:flex;align-items:center;gap:8px}
.brand-dot{width:34px;height:34px;border-radius:50%;background:var(--sky)}
.brand-name{font-weight:500;font-size:24px;color:#222;letter-spacing:1px}
.account{right:87px;top:20px;font-size:9px;color:var(--soft);display:flex;gap:8px;align-items:center}
.account .count{color:var(--blue)}
.helpline{right:86px;top:48px;font-size:9px;color:var(--soft)}
.helpline b{font-weight:400;color:var(--blue);font-size:13px}

.nav{left:79px;top:83px;width:642px;height:34px;background:linear-gradient(var(--nav-top),var(--nav-bot));border-radius:2px;display:flex;align-items:center;font-size:9px;color:#fff}
.nav a{position:absolute}
.nav .on{color:var(--sky)}

.hero{left:80px;top:118px;width:640px;height:275px;background:linear-gradient(100deg,#6e2a1c 0%,#a0563a 35%,#c48f6b 60%,#9c6a4d 100%)}
.hero-product{position:absolute;left:88px;top:30px;width:235px;height:200px;background:linear-gradient(160deg,#2a2a2a,#111);border-radius:4px}
.hero-copy{position:absolute;left:420px;top:34px;width:180px;text-align:center;color:#fff}
.hero-copy .mark{font-size:36px;font-weight:500;letter-spacing:2px}
.hero-copy .tag{font-size:17px;font-weight:300;line-height:22px;margin-top:20px}
.hero-copy .price{font-size:26px;font-weight:300;margin-top:6px}
.buy{position:absolute;left:406px;top:210px;width:110px;height:26px;background:linear-gradient(var(--gold),var(--gold-dark));border-radius:2px;font-size:11px;color:#222;display:flex;align-items:center;justify-content:center;gap:4px}
.hero svg.arrow{position:absolute;top:116px}

.main{left:80px;top:393px;width:640px;height:713px;background:var(--panel)}
.ribbon{position:absolute;left:0;top:28px}
.perk{position:absolute;top:30px;text-align:center}
.perk h3{font-weight:400;font-size:12px;color:#333}
.perk p{font-size:7px;color:var(--soft);margin-top:3px}
.perk-icon{position:absolute;top:32px;width:24px;height:24px;border-radius:50%;background:var(--sky);color:#fff;font-size:13px;display:flex;align-items:center;justify-content:center}

.section-title{position:absolute;left:7px;width:626px;top:96px;display:flex;align-items:center;gap:14px;font-size:17px;font-weight:300;color:#555}
.section-title::before,.section-title::after{content:"";flex:1;height:1px;background:var(--rule)}
.flavour{position:absolute;top:138px;width:120px;text-align:center;font-size:12px;font-weight:300;color:#444}
.flavour .swatch{width:76px;height:76px;border-radius:50%;margin:0 auto 18px;border:3px solid #eee}

.rule{position:absolute;left:7px;width:626px;height:1px;background:var(--rule)}
.welcome{position:absolute;left:40px;width:560px;top:300px;text-align:center}
.welcome h2{font-weight:300;font-size:19px;color:#444;margin-bottom:16px}
.welcome p{font-size:7.4px;line-height:12.4px;color:var(--soft);margin-bottom:12px}

.col-title{font-weight:300;font-size:13px;color:#333}
.col-title span{color:var(--blue)}
.why{position:absolute;left:10px;top:505px;width:200px}
.why ul{list-style:none;margin-top:16px}
.why li{font-size:7.6px;color:#555;line-height:16.8px;padding-left:20px;position:relative}
.why li::before{content:"→";position:absolute;left:0;color:#777}
.more{color:var(--blue);font-size:7.6px}
.news{position:absolute;left:219px;top:499px;width:202px;height:170px;background:#f1f1f2;border:1px solid #e6e6e6;padding:12px 12px}
.news .head{display:flex;justify-content:space-between}
.news .item{margin-top:16px;font-size:7.6px;line-height:12px;color:#555}
.news .item time{display:block;color:var(--blue)}
.videos{position:absolute;left:432px;top:504px;width:200px}
.video{margin-top:8px;border:1px solid #ddd;background:#fff;padding:4px;height:96px}
.video .still{position:relative;width:100%;height:100%;background:linear-gradient(120deg,#d9cfc3,#b08c74 55%,#e8e2da)}
.videos p{font-size:7.6px;line-height:12px;color:#555;margin-top:10px}

.footer{left:80px;top:1106px;width:640px;height:94px;background:linear-gradient(var(--foot-top),var(--foot-bot));color:#fff}
.foot-links{position:absolute;left:11px;top:26px;font-size:8px;display:flex;gap:7px}
.foot-links i{font-style:normal;opacity:.8}
.copy{position:absolute;left:11px;top:52px;font-size:7px}
.social{position:absolute;right:12px;top:22px;display:flex;gap:6px}
.social span{width:21px;height:21px;border-radius:50%}
.cards{position:absolute;right:12px;top:58px;display:flex;gap:6px}
.cards span{width:25px;height:14px;background:#f4f4f4;border-radius:2px}
</style>
</head>
<body>

<div class="abs brand"><span class="brand-dot"></span><span class="brand-name">PALE DUNES</span></div>
<div class="abs account">
  <svg width="16" height="14" viewBox="0 0 16 14"><path d="M1 1h3l2 8h8l1-6H5" fill="none" stroke="#666" stroke-width="1.3"/><circle cx="7" cy="12" r="1.2" fill="#666"/><circle cx="13" cy="12" r="1.2" fill="#666"/></svg>
  <span>My Cart <span class="count">(0) Item</span></span><span>|</span><span>Log In or Register</span>
</div>
<div class="abs helpline">We're here to help - call FREE, Mon-Fri 8am-8pm: <b>(014).527.3901</b></div>

<nav class="abs nav">
  <a class="on" style="left:19px">Home</a>
  <a style="left:88px">Pale Dunes Kits</a>
  <a style="left:179px">Cartridge Refills</a>
  <a style="left:272px">How it Works</a>
  <a style="left:364px">Contact</a>
  <a style="left:437px">My Account</a>
  <a style="left:524px">Checkout</a>
</nav>

<section class="abs hero">
  <div class="hero-product" role="img" aria-label="Pale Dunes starter pack box with five apple flavoured cartomisers"></div>
  <svg class="arrow" style="left:10px" width="24" height="44" viewBox="0 0 24 44"><path d="M22 2 2 22l20 20" fill="none" stroke="#fff" stroke-width="2.5"/></svg>
  <svg class="arrow" style="right:10px" width="24" height="44" viewBox="0 0 24 44"><path d="M2 2l20 20L2 42" fill="none" stroke="#fff" stroke-width="2.5"/></svg>
  <div class="hero-copy">
    <div class="mark">PALE DUNES</div>
    <div class="tag">Everything you need<br>and more</div>
    <div class="price">£29.68</div>
  </div>
  <a class="buy">Buy Now <svg width="6" height="7" viewBox="0 0 6 7"><path d="M0 0l6 3.5L0 7z" fill="#222"/></svg></a>
</section>

<main class="abs main">
  <svg class="ribbon" width="84" height="32" viewBox="0 0 84 32">
    <path d="M0 2h62l14 14-14 14H0z" fill="var(--sky)"/>
    <path d="M68 2l14 14-14 14" fill="none" stroke="var(--sky)" stroke-width="3"/>
    <text x="19" y="14" font-family="Ubuntu,sans-serif" font-size="9" fill="#fff">PALE</text>
    <text x="19" y="25" font-family="Ubuntu,sans-serif" font-size="7" fill="#fff" letter-spacing="1">DUNES</text>
  </svg>
  <div class="perk" style="left:92px;width:130px"><h3>30 DAY MONEY BACK PROMISE*</h3><p>NO QUIBBLES, HASSLE FREE RETURNS</p></div>
  <div class="perk-icon" style="left:276px">€</div>
  <div class="perk" style="left:322px;width:100px"><h3>FREE SHIPPING</h3><p>ON ORDERS £45 OR OVER</p></div>
  <svg class="abs" style="left:432px;top:32px" width="26" height="26" viewBox="0 0 26 26"><path d="M3 8l10-5 10 5v12l-10 5-10-5z" fill="var(--sky)"/><path d="M3 8l10 5 10-5M13 13v12" stroke="#fff" stroke-width="1" fill="none"/></svg>
  <div class="perk" style="left:482px;width:110px"><h3>1 YEAR WARRANTY*</h3><p>FOR YOUR PEACE OF MIND</p></div>
  <div class="perk-icon" style="left:608px">1</div>

  <h2 class="section-title">FLAVOURS</h2>
  <div class="flavour" style="left:-7px"><div class="swatch" role="img" aria-label="Cut tobacco rolls" style="background:radial-gradient(#c4894e,#7a4620)"></div>CLASSIC TOBACCO</div>
  <div class="flavour" style="left:127px"><div class="swatch" role="img" aria-label="Golden shredded tobacco" style="background:radial-gradient(#e6b35f,#b97a2a)"></div>TOBACCO GOLD</div>
  <div class="flavour" style="left:261px"><div class="swatch" role="img" aria-label="Fresh mint leaves" style="background:radial-gradient(#8bd660,#2f8a2a)"></div>MENTHOL</div>
  <div class="flavour" style="left:394px"><div class="swatch" role="img" aria-label="Cinnamon sticks" style="background:radial-gradient(#fff 30%,#9a5a30 70%)"></div>CINNAMON</div>
  <div class="flavour" style="left:527px"><div class="swatch" role="img" aria-label="Bunch of red cherries" style="background:radial-gradient(#e63b3b,#9c1010)"></div>CHERRY</div>

  <div class="rule" style="top:274px"></div>
  <div class="welcome">
    <h2>Welcome to Pale Dunes</h2>
    <p>Sed ut perspiciatis unde omnis iste natus error sit voluptatem accusantium doloremque laudantium, totam rem aperiam, eaque ipsa quae ab illo inventore veritatis et quasi architecto beatae vitae dicta sunt explicabo. Nemo enim ipsam voluptatem quia voluptas sit aspernatur aut odit aut fugit, sed quia consequuntur magni dolores eos qui ratione voluptatem sequi nesciunt.</p>
    <p>Neque porro quisquam est, qui dolorem ipsum quia dolor sit amet, consectetur, adipisci velit, sed quia non numquam eius modi tempora incidunt ut labore et dolore magnam aliquam quaerat voluptatem. Ut enim ad minima veniam, quis nostrum exercitationem ullam corporis suscipit laboriosam, nisi ut aliquid ex ea commodi consequatur? Quis autem vel eum iure reprehenderit qui in ea voluptate velit esse quam nihil molestiae consequatur, vel illum qui dolorem eum fugiat quo voluptas nulla pariatur</p>
  </div>
  <div class="rule" style="top:470px"></div>

  <div class="why">
    <h3 class="col-title">Why use <span>Pale Dunes?</span></h3>
    <ul>
      <li>Named UK's No.1 e-cigarette by Fumelist.com</li>
      <li>30-day "no quibbles" money-back promise</li>
      <li>Over 300,000+ customers</li>
      <li>Friendly, UK-based customer services</li>
      <li>Industry-leading technology</li>
    </ul>
    <a class="more" style="display:block;margin:6px 0 0 20px">Get Started &gt;&gt;</a>
  </div>

  <div class="news">
    <div class="head"><h3 class="col-title" style="font-size:14px">Latest News</h3><span style="font-size:13px;color:#555">‹ ›</span></div>
    <div class="item"><time>21 Nov 2013</time>Setting goals - is it an important part of quitting tobacco? <a>more&gt;&gt;</a></div>
    <div class="item"><time>21 Nov 2013</time>Setting goals - is it an important part of quitting tobacco? Setting goals - is it an important part of quitting tobacco? <a>more&gt;&gt;</a></div>
  </div>

  <div class="videos">
    <h3 class="col-title">Watch Video's</h3>
    <div class="video"><div class="still" role="img" aria-label="Video still of two men in a kitchen">
      <svg class="abs" style="left:70px;top:14px" width="60" height="60" viewBox="0 0 60 60"><circle cx="30" cy="30" r="29" fill="#fff" opacity=".6"/><path d="M23 17l20 13-20 13z" fill="#e0322b"/></svg>
    </div></div>
    <p>Excepteur sint occaecat cupidatat non proident, sunt in culpa qui officia deserunt mollit anim</p>
    <a class="more">more &gt;&gt;</a>
  </div>
</main>

<footer class="abs footer">
  <div class="foot-links"><a>Home</a><i>|</i><a>Pale Dunes Kits</a><i>|</i><a>Cartridge Refills</a><i>|</i><a>How it Works</a><i>|</i><a>Contact</a><i>|</i><a>My Account</a><i>|</i><a>Checkout</a></div>
  <div class="copy">Copyright ©2013 Pale Dunes Vapour Co. All Rights Reserved.</div>
  <div class="social"><span style="background:#2f5aa8"></span><span style="background:#2aa6e0"></span><span style="background:#555"></span><span style="background:#f59a12"></span></div>
  <div class="cards"><span></span><span></span><span></span><span></span></div>
</footer>

</body>
</html>
```